NZ First of it's kind solutions directory and marketplace for busy Mums needs a business card design

We need a business card design for our new nationwide business in NZ (long term plans to go global). We provide solutions to the everyday challenges that busy Mums face by connecting them with quality communities and suppliers of carefully selected, relevant products and services. We sell direct via our online marketplace. The final design should communicate our values of inclusivity, quality and smart solutions. Colours should incorporate our logo colour palette of #477077 and #6ba8b2. Our website is at https://www.brightnestmums.example

Target Market(s)

busy Mums, Age 28 – 50, female, income over $100K, location main centres NZ primarily but NZ wide. Is likely juggling work or career with a young family. Probably had hobbies which have fallen by the wayside.
-Wants to succeed in her chosen career without compromising on family life
-to successfully juggle her career without feeling like she is compromising her children
- Is time poor, something always has to give and it’s generally her health (she’ll stay up late, get stressed)
- probably ex corporate or professional career. Has discretional income

Industry/Entity Type

Business

Contact Information for Business Card

Lena Forbisher, Founder, BrightNestMums.example (Strapline Tap; Gather; Sorted), 47 Kowhai Terrace, Ellerslie, Auckland 1051, New Zealand. Mob: 021 483 517 Ph: +64 (0)9 571 4860

Font styles to use
Other font styles liked:
• Raleway, and/or Architects Daughter

Colors
00a990
33b8a4
86cfc6
cfeae6

Requirements
Must have
• the above details, streamline. the logo and colours associated with those logos
Should not have
• foil or metallic colours

```html
<!DOCTYPE html>
<html lang="en">
<head>
<meta charset="utf-8">
<title>BrightNestMums business card</title>
<link rel="stylesheet" href="https://fonts.googleapis.com/css2?family=Roboto:ital,wght@0,400;0,500;1,400&display=swap">
<style>
  :root {
    --teal-deep: #3f646b;
    --teal-light: #6ba8b2;
    --ink: #3a3a3a;
    --paper: #ffffff;
    --backdrop: #e4e4e4;
  }
  * { box-sizing: border-box; margin: 0; padding: 0; }
  html, body {
    width: 1200px; height: 576px; overflow: hidden;
    background: var(--backdrop);
    font-family: "Roboto", Arial, sans-serif;
    color: var(--ink);
  }
  .canvas { position: relative; width: 1200px; height: 576px; }
  .card {
    position: absolute; top: 138px;
    width: 485px; height: 294px;
    background: var(--paper);
    border-radius: 14px;
    overflow: hidden;
  }
  .card--front { left: 82px; }
  .card--back { left: 602px; }

  .brand-name {
    font-weight: 500;
    color: var(--teal-deep);
    letter-spacing: -0.5px;
    line-height: 1;
  }
  .strapline {
    font-size: 10px;
    letter-spacing: 4.2px;
    text-transform: uppercase;
    color: var(--ink);
    white-space: nowrap;
  }
  .strapline .divider { color: var(--teal-light); margin: 0 6px; }

  .card--front .brand-block {
    position: absolute; left: 0; right: 0; top: 165px;
    text-align: center;
  }
  .card--front .brand-name { font-size: 31px; }
  .card--front .strapline { margin-top: 10px; }

  .card--back .brand-block { position: absolute; left: 26px; top: 30px; }
  .card--back .brand-name { font-size: 29px; }
  .card--back .strapline { margin-top: 11px; font-size: 9.5px; }

  .address {
    position: absolute; left: 26px; top: 158px;
    font-size: 12px; line-height: 18.5px;
  }
  .contact-list {
    position: absolute; left: 26px; top: 204px;
    list-style: none; font-size: 12px; line-height: 18.5px;
  }
  .contact-list li { display: flex; align-items: center; gap: 8px; }
  .contact-list svg { width: 10px; height: 10px; flex: none; }

  .name-panel {
    position: absolute; left: 278px; top: 92px; right: 0; bottom: 0;
    background: var(--teal-deep);
  }
  .person {
    position: absolute; left: 278px; right: 0; top: 222px;
    text-align: center; color: var(--paper);
  }
  .person__name { font-size: 19px; font-weight: 500; }
  .person__role { font-size: 11px; font-style: italic; margin-top: 2px; }
</style>
</head>
<body>
<main class="canvas">

  <section class="card card--front" aria-label="Card front">
    <div class="brand-block">
      <p class="brand-name">BrightNestMums</p>
      <p class="strapline">Tap<span class="divider">|</span>Gather<span class="divider">|</span>Sorted</p>
    </div>
  </section>

  <section class="card card--back" aria-label="Card back">
    <div class="brand-block">
      <p class="brand-name">BrightNestMums</p>
      <p class="strapline">Tap<span class="divider">|</span>Gather<span class="divider">|</span>Sorted</p>
    </div>

    <address class="address" style="font-style:normal">
      47 Kowhai Terrace, Ellerslie,<br>
      Auckland 1051, New Zealand
    </address>

    <ul class="contact-list">
      <li>
        <svg viewBox="0 0 10 10" aria-hidden="true"><rect x="2.5" y="0.5" width="5" height="9" rx="1" fill="none" stroke="var(--teal-light)" stroke-width="1.2"/><circle cx="5" cy="7.8" r="0.6" fill="var(--teal-light)"/></svg>
        021 483 517
      </li>
      <li>
        <svg viewBox="0 0 10 10" aria-hidden="true"><path d="M1 3.5 Q5 0.5 9 3.5 L8 5 L6.5 4 L6.5 3 Q5 2.5 3.5 3 L3.5 4 L2 5 Z" fill="var(--teal-light)"/><rect x="2" y="5.5" width="6" height="3.5" rx="0.6" fill="var(--teal-light)"/></svg>
        +64 (0)9 571 4860
      </li>
      <li>
        <svg viewBox="0 0 10 10" aria-hidden="true"><rect x="0.8" y="2" width="8.4" height="6" fill="none" stroke="var(--teal-light)" stroke-width="1.1"/><path d="M0.8 2 L5 5.5 L9.2 2" fill="none" stroke="var(--teal-light)" stroke-width="1.1"/></svg>
        www.BrightNestMums.example
      </li>
      <li>
        <svg viewBox="0 0 10 10" aria-hidden="true"><circle cx="5" cy="5" r="4.2" fill="none" stroke="var(--teal-light)" stroke-width="1"/><ellipse cx="5" cy="5" rx="1.8" ry="4.2" fill="none" stroke="var(--teal-light)" stroke-width="0.8"/><line x1="0.8" y1="5" x2="9.2" y2="5" stroke="var(--teal-light)" stroke-width="0.8"/></svg>
        lena@brightnestmums.example
      </li>
    </ul>

    <div class="name-panel"></div>
    <div class="person">
      <p class="person__name">Lena Forbisher</p>
      <p class="person__role">Founder</p>
    </div>
  </section>

</main>
</body>
</html>
```